Business card design

We need a business card designed completed for a new company. We are a company that works with associations, schools to convert their older text/DVDs into dynamic online and mobile programs. Our initial platform is designed for the legal associations and will enable their lawyers to access their content such as forms, videos, case law and support materials anywhere, anytime. We are also focused on Project Management Associations, Financial Management Associations and IT Associations.

I would like for the business card to have the following information:

Logo

Kent marrowby

President and CEO

kmarrowby@trevantiq.example

Mobile: 555-374-9160

www.trevantiq.example

Tag line: Transforming content into a mobile platform    

I would like it to be double sided, use the colours of the logo, tie into the mobile world

 

Industry/Entity Type

Legal

Logo Text

Trevantiq

```html
<!DOCTYPE html>
<html lang="en">
<head>
<meta charset="utf-8">
<title>Trevantiq business card</title>
<link rel="stylesheet" href="https://fonts.googleapis.com/css2?family=Open+Sans:ital,wght@0,400;0,700;0,800;1,700&display=swap">
<style>
  :root {
    --backdrop: #b8906c;
    --label: #1c1c1c;
    --card-grey: #959595;
    --card-white: #ffffff;
    --band-dark: #343434;
    --band-light: #9c9c9c;
    --footer-grey: #626262;
    --ink-white: #ffffff;
    --ink-dark: #222222;
    --ink-mid: #5a5a5a;
    --mark-dark: #6a6a6a;
  }
  * { margin: 0; padding: 0; box-sizing: border-box; }
  html, body { width: 1200px; height: 800px; overflow: hidden; }
  body {
    position: relative;
    background: var(--backdrop);
    font-family: "Open Sans", Arial, sans-serif;
  }
  .side-label {
    position: absolute;
    width: 300px;
    text-align: center;
    font-size: 21px;
    color: var(--label);
  }
  .card {
    position: absolute;
    width: 510px;
    height: 290px;
    border-radius: 18px;
    overflow: hidden;
  }
  .card--grey { background: var(--card-grey); }
  .card--white { background: var(--card-white); }

  .wordmark {
    position: absolute;
    left: 0; right: 0;
    text-align: center;
    font-weight: 800;
    line-height: 1;
    letter-spacing: -0.5px;
  }
  .card--grey .wordmark { color: var(--ink-white); }
  .card--white .wordmark { color: var(--mark-dark); }
  .card--detail .wordmark { top: 67px; font-size: 50px; }
  .card--plain .wordmark { top: 100px; font-size: 82px; }

  .tagline {
    position: absolute;
    top: 148px; left: 0; right: 0;
    text-align: center;
    font-size: 15px;
  }
  .card--grey .tagline { color: var(--ink-white); }
  .card--white .tagline { color: var(--ink-mid); }

  .name-band {
    position: absolute;
    top: 182px; left: 0; right: 0;
    height: 32px;
    display: flex; align-items: center; justify-content: center;
    font-size: 15px;
  }
  .name-band .role { font-size: 12px; margin-left: 4px; }
  .card--grey .name-band { background: var(--band-dark); color: var(--ink-white); }
  .card--white .name-band { background: var(--band-light); color: var(--ink-dark); }

  .contact-block {
    position: absolute;
    top: 220px; left: 0; right: 0; bottom: 0;
    background: var(--footer-grey);
    color: var(--ink-white);
    font-size: 13px;
    text-align: center;
    padding-top: 14px;
    line-height: 23px;
  }
  .contact-block b { font-style: italic; font-weight: 700; }

  .web-line {
    position: absolute;
    bottom: 18px; left: 0; right: 0;
    text-align: center;
    font-size: 15px;
    letter-spacing: 3px;
    color: var(--ink-dark);
  }
</style>
</head>
<body>
  <div class="side-label" style="left:179px; top:50px;">Front</div>
  <div class="side-label" style="left:737px; top:50px;">Back - 1</div>
  <div class="side-label" style="left:179px; top:410px;">Back - 2</div>
  <div class="side-label" style="left:737px; top:410px;">Back - 3</div>

  <section class="card card--grey card--detail" style="left:80px; top:97px;">
    <div class="wordmark">Trevantiq</div>
    <p class="tagline">Transforming content into a mobile platform</p>
    <div class="name-band">Kent marrowby,<span class="role">President and CEO</span></div>
    <div class="contact-block">
      <div><b>c</b> : 555-374-9160</div>
      <div><b>e</b> : kmarrowby@trevantiq.example | <b>w</b> : www.trevantiq.example</div>
    </div>
  </section>

  <section class="card card--white card--detail" style="left:630px; top:97px;">
    <div class="wordmark">Trevantiq</div>
    <p class="tagline">Transforming content into a mobile platform</p>
    <div class="name-band">Kent marrowby,<span class="role">President and CEO</span></div>
    <div class="contact-block">
      <div><b>c</b> : 555-374-9160</div>
      <div><b>e</b> : kmarrowby@trevantiq.example | <b>w</b> : www.trevantiq.example</div>
    </div>
  </section>

  <section class="card card--grey card--plain" style="left:73px; top:452px;">
    <div class="wordmark">Trevantiq</div>
    <p class="web-line">www.trevantiq.example</p>
  </section>

  <section class="card card--white card--plain" style="left:634px; top:450px;">
    <div class="wordmark">Trevantiq</div>
    <p class="web-line">www.trevantiq.example</p>
  </section>
</body>
</html>
```